Brightmill Data Works

Our company is about IT hardwares and IT solutions. IT hardware such as PC, RAMS, storage and servers. IT solutions such as project management, BA. We are also selling new technology too.

Target Market(s)

Consumer, Small to Medium Business, Corporate

Requirements
Must have
• The business card must have the following:
• Name:
• Title:
• Contact Number:
• Email address:
• Website:
• Color: Must match the logo color upgrade

```html
<!DOCTYPE html>
<html lang="en">
<head>
<meta charset="utf-8">
<title>Brightmill Data Works – Business Card</title>
<link rel="stylesheet" href="https://fonts.googleapis.com/css2?family=Arimo:wght@400;700&family=Saira:wght@700&display=swap">
<style>
  :root {
    --stage: #2b2b2b;
    --card-dark: #2e2e30;
    --card-light: #f2f2f2;
    --accent: #d9761e;
    --ink: #3a3a3c;
    --ink-soft: #1e1e1e;
    --white: #ffffff;
  }
  * { margin: 0; padding: 0; box-sizing: border-box; }
  html, body { width: 1200px; height: 997px; overflow: hidden; }
  body {
    background: var(--stage);
    position: relative;
    font-family: "Arimo", Arial, sans-serif;
  }
  .card {
    position: absolute;
    width: 560px;
    height: 320px;
    border-radius: 22px;
    overflow: hidden;
  }
  .card-back {
    left: 110px;
    top: 110px;
    background: var(--card-dark);
    display: flex;
    align-items: center;
    justify-content: center;
    gap: 18px;
  }
  .card-front {
    left: 530px;
    top: 540px;
    background: var(--card-dark);
  }
  .card-front .sweep {
    position: absolute;
    inset: 0;
    width: 100%;
    height: 100%;
  }
  .brand-dot {
    width: 22px;
    height: 22px;
    border-radius: 50%;
    background: var(--accent);
    flex: none;
  }
  .brand-name {
    font-family: "Saira", "Arial Black", sans-serif;
    font-weight: 700;
    text-transform: uppercase;
    letter-spacing: 1px;
    line-height: 1.05;
  }
  .card-back .brand-name {
    color: var(--white);
    font-size: 40px;
  }
  .front-brand {
    position: absolute;
    right: 30px;
    top: 70px;
    display: flex;
    align-items: center;
    gap: 12px;
  }
  .front-brand .brand-name {
    color: var(--ink);
    font-size: 28px;
  }
  .front-brand .brand-dot { width: 18px; height: 18px; }
  .person {
    position: absolute;
    left: 26px;
    top: 30px;
  }
  .person-name {
    color: var(--accent);
    font-weight: 700;
    font-size: 19px;
  }
  .person-title {
    color: var(--white);
    font-size: 15px;
    margin-top: 4px;
  }
  .contacts {
    position: absolute;
    right: 24px;
    bottom: 30px;
    list-style: none;
    color: var(--ink-soft);
    font-size: 13.5px;
    line-height: 24px;
  }
  .contacts li {
    display: flex;
    justify-content: flex-end;
    align-items: center;
    gap: 8px;
  }
  .contact-icon {
    width: 17px;
    height: 17px;
    border-radius: 50%;
    background: var(--ink);
    display: inline-flex;
    align-items: center;
    justify-content: center;
    flex: none;
  }
</style>
</head>
<body>

  <section class="card card-back" aria-label="Card back">
    <span class="brand-dot"></span>
    <span class="brand-name">Brightmill<br>Data Works</span>
  </section>

  <section class="card card-front" aria-label="Card front">
    <svg class="sweep" viewBox="0 0 560 320" preserveAspectRatio="none" aria-hidden="true">
      <path d="M40 320 C120 130 300 30 560 4 L560 320 Z" fill="#e8e8e8"/>
      <path d="M56 320 C140 135 310 38 560 10 L560 320 Z" fill="#d9761e"/>
      <path d="M80 320 C160 150 330 48 560 22 L560 320 Z" fill="#f2f2f2"/>
    </svg>

    <div class="person">
      <p class="person-name">Daniel R.Whitford</p>
      <p class="person-title">Managing Director</p>
    </div>

    <div class="front-brand">
      <span class="brand-dot"></span>
      <span class="brand-name">Brightmill<br>Data Works</span>
    </div>

    <ul class="contacts">
      <li>(555) 214-6093
        <span class="contact-icon">
          <svg width="10" height="10" viewBox="0 0 10 10"><path d="M2 1 L4 1 L4.6 3 L3.4 3.8 C4 5.2 4.8 6 6.2 6.6 L7 5.4 L9 6 L9 8 C5 8.4 1.6 5 2 1 Z" fill="#fff"/></svg>
        </span>
      </li>
      <li>whitford@brightmilldata.com
        <span class="contact-icon">
          <svg width="10" height="8" viewBox="0 0 10 8"><rect x="0.5" y="0.5" width="9" height="7" fill="none" stroke="#fff"/><path d="M0.5 0.5 L5 4.5 L9.5 0.5" fill="none" stroke="#fff"/></svg>
        </span>
      </li>
      <li>www.brightmilldata.com
        <span class="contact-icon">
          <svg width="10" height="10" viewBox="0 0 10 10"><circle cx="5" cy="5" r="4" fill="none" stroke="#fff"/><path d="M1 5 H9 M5 1 C3 3 3 7 5 9 M5 1 C7 3 7 7 5 9" fill="none" stroke="#fff" stroke-width="0.8"/></svg>
        </span>
      </li>
    </ul>
  </section>

</body>
</html>
```